Design a website for a quickly growing ghostwriting and editing firm

DWB Productions has a website through Wix, but we need help! We are based in Austin, TX, and we work primarily with self-help, wellness, and diet authors. We offer ghostwriting, editing and book development services. You can see our basic site now at www.dorawhitbyproductions.com

```html
<!DOCTYPE html>
<html lang="en">
<head>
<meta charset="utf-8">
<title>DWB Productions – Homepage Concepts</title>
<link href="https://fonts.googleapis.com/css2?family=Josefin+Sans:wght@300;400&family=Roboto:wght@400;500;700&display=swap" rel="stylesheet">
<style>
:root{
  --board:#bdbdbd;
  --gold:#b5651d;
  --gold-dark:#9c5416;
  --ink:#222222;
  --muted:#8a8a8a;
  --cream:#fbf3ea;
  --line:#e6e1da;
  --footer:#2d2d2d;
  --white:#ffffff;
}
*{box-sizing:border-box;margin:0;padding:0}
html,body{width:997px;height:1200px;overflow:hidden}
body{background:var(--board);font-family:"Roboto",Arial,sans-serif;color:var(--ink)}
.board{position:relative;width:997px;height:1200px;background:var(--board)}
.page{position:absolute;top:54px;width:439px;height:1091px;background:var(--white);overflow:hidden}
.page--photo{left:50px}
.page--line-art{left:508px}

/* header */
.site-header{position:absolute;top:0;left:0;width:100%;height:33px;background:var(--white)}
.brand{position:absolute;left:52px;top:9px;display:flex;align-items:center;gap:4px}
.brand__dot{width:14px;height:14px;border-radius:50%;background:var(--gold)}
.brand__name{font-family:"Josefin Sans",sans-serif;font-weight:400;font-size:9px;color:var(--ink);letter-spacing:.3px}
.main-nav{position:absolute;left:187px;top:0;height:33px;display:flex;align-items:center;gap:9px}
.main-nav a{font-size:5.2px;font-weight:500;color:var(--ink);text-decoration:none;text-transform:uppercase;position:relative}
.main-nav a.is-active::after{content:"";position:absolute;left:0;right:0;bottom:-4px;height:1.2px;background:var(--gold)}
.login-btn{position:absolute;left:347px;top:8px;width:39px;height:16px;border-radius:8px;background:var(--gold);color:var(--white);font-size:5.2px;font-weight:500;display:flex;align-items:center;justify-content:center}

/* hero */
.hero{position:absolute;top:33px;left:0;width:100%;height:199px;
  background:linear-gradient(180deg,#d9e8f2 0%,#9fc0cf 10%,#5f8f63 26%,#3f7446 44%,#4c7a4a 54%,#1f8c95 62%,#0f7983 78%,#0a5f68 100%)}
.hero__title{position:absolute;left:0;width:100%;text-align:center;font-family:"Roboto",sans-serif;font-weight:700;color:#c9781e;line-height:1}
.hero__title--top{top:62px;font-size:34px}
.hero__title--bottom{top:102px;font-size:34px}
.scroll-cue{position:absolute;left:214px;top:167px}

/* section headings */
.section-title{position:absolute;left:0;width:100%;text-align:center;font-family:"Josefin Sans",sans-serif;font-weight:300;font-size:20px;letter-spacing:.5px;color:var(--ink)}

/* offers */
.offers{position:absolute;top:232px;left:0;width:100%;height:283px;background:var(--white)}
.offers .section-title{top:31px}
.offer-grid{position:absolute;top:74px;left:52px;width:334px;height:179px;display:grid;grid-template-columns:repeat(3,1fr);grid-template-rows:repeat(2,1fr);border:0.5px solid var(--line)}
.offer-card{background:var(--white);display:flex;flex-direction:column;align-items:center;padding-top:14px;text-align:center;border:0.5px solid var(--line)}
.offer-card__title{font-size:8px;font-weight:700;text-transform:uppercase;color:var(--ink);margin-bottom:6px}
.offer-card__text{font-size:4.6px;line-height:1.75;color:var(--muted);width:92px;margin-bottom:6px}
.offer-visual{width:100%;height:100%}
.page--photo .offer-visual--manuscript{background:linear-gradient(150deg,#cfdbe0 0%,#f1ece4 40%,#e9c9a8 80%,#c99a6a 100%)}
.page--photo .offer-visual--open-book{background:linear-gradient(160deg,#6b5546 0%,#3f3129 45%,#cdbca8 80%,#8e6f56 100%)}
.page--photo .offer-visual--laptop{background:linear-gradient(160deg,#dfe7ee 0%,#b9c5cf 45%,#8a97a2 80%,#cfc7bf 100%)}
.page--line-art .offer-visual{background:var(--cream)}

/* buttons */
.btn{display:inline-flex;align-items:center;gap:3px;background:var(--gold);color:var(--white);border-radius:7px;font-weight:500;text-transform:uppercase;white-space:nowrap}
.btn--small{height:12px;padding:0 7px;font-size:4.6px}
.btn--large{height:17px;padding:0 10px;font-size:6px;border-radius:9px}
.btn svg{display:block}

/* about */
.about{position:absolute;top:515px;left:0;width:100%;height:215px;background:var(--cream)}
.about .section-title{top:39px}
.about__text{position:absolute;top:71px;left:130px;width:179px;text-align:center;font-size:4.6px;line-height:2;color:var(--muted)}
.about .btn{position:absolute;top:155px;left:187px}

/* contact */
.contact{position:absolute;top:730px;left:0;width:100%;height:224px;background:var(--white)}
.contact__scene{position:absolute;left:0;top:48px;width:100%;height:176px;
  background:linear-gradient(180deg,#ffffff 0%,#eee6f0 14%,#c7b3cf 30%,#a58ab4 42%,#8f76a6 48%,#d9d2e6 58%,#b9a7cb 72%,#e7e2ee 100%)}
.contact .section-title{top:40px}
.contact-form{position:absolute;top:73px;left:85px;width:268px}
.field{position:absolute;height:19px;background:var(--white);border:0.5px solid #d9d3dd;font-size:5.4px;color:#555;padding:0 8px;display:flex;align-items:center}
.field--first{left:0;top:0;width:132px}
.field--last{left:136px;top:0;width:132px}
.field--email{left:0;top:23px;width:132px}
.field--phone{left:136px;top:23px;width:132px}
.field--message{left:0;top:48px;width:268px;height:41px;align-items:flex-start;padding-top:7px}
.contact .btn{position:absolute;top:177px;left:187px}

/* footer */
.site-footer{position:absolute;top:954px;left:0;width:100%;height:137px;background:var(--footer);color:var(--white)}
.site-footer .brand{left:0;width:100%;top:20px;justify-content:center;gap:5px}
.site-footer .brand__dot{width:20px;height:20px}
.site-footer .brand__name{font-size:12px;color:var(--white)}
.footer-contacts{position:absolute;top:61px;left:85px;display:flex;align-items:center;font-size:4.6px;line-height:1.7}
.footer-contacts__item{display:flex;align-items:center;gap:6px;margin-right:13px}
.footer-contacts__icon{width:14px;height:14px;border:0.8px solid #9a9a9a;border-radius:50%;display:flex;align-items:center;justify-content:center}
.footer-nav{position:absolute;top:94px;left:0;width:100%;display:flex;justify-content:center;gap:4px;font-size:6.6px;font-weight:500;text-transform:uppercase}
.footer-nav span{color:var(--white)}
.copyright{position:absolute;top:113px;left:0;width:100%;text-align:center;font-size:4.6px;color:#d6d6d6}
</style>
</head>
<body>
<main class="board">

  <!-- concept A: photographic service tiles -->
  <section class="page page--photo">
    <header class="site-header">
      <div class="brand"><span class="brand__dot"></span><span class="brand__name">DWB Productions</span></div>
      <nav class="main-nav">
        <a class="is-active">Home</a><a>About</a><a>Services</a><a>News</a><a>Contact</a>
      </nav>
      <span class="login-btn">LOGIN</span>
    </header>

    <div class="hero" role="img" aria-label="Mountain lake with forested green slopes under a pale sky">
      <div class="hero__title hero__title--top">DWB</div>
      <div class="hero__title hero__title--bottom">PRODUCTIONS</div>
      <svg class="scroll-cue" width="10" height="20" viewBox="0 0 10 20"><rect x="1.5" y="1" width="7" height="11" rx="3.5" fill="none" stroke="#fff" stroke-width="0.8"/><line x1="5" y1="3.5" x2="5" y2="6" stroke="#fff" stroke-width="0.8"/><polyline points="2,15 5,18 8,15" fill="none" stroke="#fff" stroke-width="0.8"/></svg>
    </div>

    <section class="offers">
      <h2 class="section-title">WHAT WE OFFER</h2>
      <div class="offer-grid">
        <div class="offer-visual offer-visual--manuscript" role="img" aria-label="Photo of a hand marking up a printed manuscript with a red pen"></div>
        <article class="offer-card">
          <h3 class="offer-card__title">Ghostwriting</h3>
          <p class="offer-card__text">At vero eos et accusamus et iusto odio dignissiducimumos ducimus qui blanditiis pducimuducimuraesentiu</p>
          <span class="btn btn--small">Read more <svg width="5" height="5" viewBox="0 0 10 10"><circle cx="5" cy="5" r="5" fill="#fff"/><path d="M4 2.5 6.5 5 4 7.5" fill="none" stroke="#b5651d" stroke-width="1.6"/></svg></span>
        </article>
        <div class="offer-visual offer-visual--open-book" role="img" aria-label="Photo of an open book on a wooden table"></div>
        <article class="offer-card">
          <h3 class="offer-card__title">Editing</h3>
          <p class="offer-card__text">At vero eos et accusamus et iusto odio dignissiducimumos ducimus qui blanditiis pducimuducimuraesentiu</p>
          <span class="btn btn--small">Read more <svg width="5" height="5" viewBox="0 0 10 10"><circle cx="5" cy="5" r="5" fill="#fff"/><path d="M4 2.5 6.5 5 4 7.5" fill="none" stroke="#b5651d" stroke-width="1.6"/></svg></span>
        </article>
        <div class="offer-visual offer-visual--laptop" role="img" aria-label="Photo of hands typing on a laptop while holding a phone"></div>
        <article class="offer-card">
          <h3 class="offer-card__title">Book Development</h3>
          <p class="offer-card__text">At vero eos et accusamus et iusto odio dignissiducimumos ducimus qui blanditiis pducimuducimuraesentiu</p>
          <span class="btn btn--small">Read more <svg width="5" height="5" viewBox="0 0 10 10"><circle cx="5" cy="5" r="5" fill="#fff"/><path d="M4 2.5 6.5 5 4 7.5" fill="none" stroke="#b5651d" stroke-width="1.6"/></svg></span>
        </article>
      </div>
    </section>

    <section class="about">
      <h2 class="section-title">ABOUT US</h2>
      <p class="about__text">Lorem ipsum dolor sit amet, consectetur adipiscing elit, sed do eiusmod tempor incididunt ut labore et dolore magna aliqua. Quis ipsum suspendisse ultrices gravida. Risus commodo viverra maecenas accumsan lacus vel facilisisLorem ipsum dolor sit amet, consectetur adipiscing elit, sed do eiusmod tempor incididunt ut labore et dolore magna aliqua. Quis ipsum suspendisse ultrices gravida. Risus commodo viverra maecenas accumsan lacus vel facilisis. Lorem ipsum dolor sit amet, consectetur adipiscing elit, sed do eiusmod tempor incididunt ut labore et dolore magna aliqua.is ipsum suspendisse ultrices gravida</p>
      <span class="btn btn--large">Read more <svg width="6" height="6" viewBox="0 0 10 10"><circle cx="5" cy="5" r="5" fill="#fff"/><path d="M4 2.5 6.5 5 4 7.5" fill="none" stroke="#b5651d" stroke-width="1.6"/></svg></span>
    </section>

    <section class="contact">
      <div class="contact__scene" role="img" aria-label="Misty lavender lake at dawn with a person stretching on the shore"></div>
      <h2 class="section-title">CONTACT FORM</h2>
      <form class="contact-form">
        <div class="field field--first">First Name</div>
        <div class="field field--last">Last Name</div>
        <div class="field field--email">Email address</div>
        <div class="field field--phone">Phone Number</div>
        <div class="field field--message">Message</div>
      </form>
      <span class="btn btn--large">Submit <svg width="6" height="6" viewBox="0 0 10 10"><circle cx="5" cy="5" r="5" fill="#fff"/><path d="M4 2.5 6.5 5 4 7.5" fill="none" stroke="#b5651d" stroke-width="1.6"/></svg></span>
    </section>

    <footer class="site-footer">
      <div class="brand"><span class="brand__dot"></span><span class="brand__name">DWB Productions</span></div>
      <div class="footer-contacts">
        <div class="footer-contacts__item"><span class="footer-contacts__icon"><svg width="6" height="7" viewBox="0 0 12 14"><path d="M6 13S1 7.5 1 5a5 5 0 0 1 10 0c0 2.5-5 8-5 8z" fill="#fff"/><circle cx="6" cy="5" r="1.8" fill="#2d2d2d"/></svg></span><span>314,At vero eos et accu<br>samus et iusto odio dimos ducimu</span></div>
        <div class="footer-contacts__item"><span class="footer-contacts__icon"><svg width="6" height="6" viewBox="0 0 12 12"><path d="M2.5 1 4.5 3.5 3.3 5a7 7 0 0 0 3.7 3.7L8.5 7.5 11 9.5 10 11C5 11 1 7 1 2z" fill="#fff"/></svg></span><span>1 888 888 8888</span></div>
        <div class="footer-contacts__item"><span class="footer-contacts__icon"><svg width="7" height="5" viewBox="0 0 14 10"><rect width="14" height="10" rx="1" fill="#fff"/><path d="M1 1.5 7 6 13 1.5" fill="none" stroke="#2d2d2d" stroke-width="1.2"/></svg></span><span>info@dorawhitbyproductions.com</span></div>
      </div>
      <nav class="footer-nav"><span>Home</span> / <span>About</span> / <span>Services</span> / <span>News</span> / <span>Contact</span></nav>
      <p class="copyright">© 2021 DWB Productions. All rights reserved.Privacy Terms of Use</p>
    </footer>
  </section>

  <!-- concept B: line-art service tiles -->
  <section class="page page--line-art">
    <header class="site-header">
      <div class="brand"><span class="brand__dot"></span><span class="brand__name">DWB Productions</span></div>
      <nav class="main-nav">
        <a class="is-active">Home</a><a>About</a><a>Services</a><a>News</a><a>Contact</a>
      </nav>
      <span class="login-btn">LOGIN</span>
    </header>

    <div class="hero" role="img" aria-label="Mountain lake with forested green slopes under a pale sky">
      <div class="hero__title hero__title--top">DWB</div>
      <div class="hero__title hero__title--bottom">PRODUCTIONS</div>
      <svg class="scroll-cue" width="10" height="20" viewBox="0 0 10 20"><rect x="1.5" y="1" width="7" height="11" rx="3.5" fill="none" stroke="#fff" stroke-width="0.8"/><line x1="5" y1="3.5" x2="5" y2="6" stroke="#fff" stroke-width="0.8"/><polyline points="2,15 5,18 8,15" fill="none" stroke="#fff" stroke-width="0.8"/></svg>
    </div>

    <section class="offers">
      <h2 class="section-title">WHAT WE OFFER</h2>
      <div class="offer-grid">
        <div class="offer-visual" role="img" aria-label="Line drawing of hands writing on a tablet"></div>
        <article class="offer-card">
          <h3 class="offer-card__title">Ghostwriting</h3>
          <p class="offer-card__text">At vero eos et accusamus et iusto odio dignissiducimumos ducimus qui blanditiis pducimuducimuraesentiu</p>
          <span class="btn btn--small">Read more <svg width="5" height="5" viewBox="0 0 10 10"><circle cx="5" cy="5" r="5" fill="#fff"/><path d="M4 2.5 6.5 5 4 7.5" fill="none" stroke="#b5651d" stroke-width="1.6"/></svg></span>
        </article>
        <div class="offer-visual" role="img" aria-label="Line drawing of a closed book"></div>
        <article class="offer-card">
          <h3 class="offer-card__title">Editing</h3>
          <p class="offer-card__text">At vero eos et accusamus et iusto odio dignissiducimumos ducimus qui blanditiis pducimuducimuraesentiu</p>
          <span class="btn btn--small">Read more <svg width="5" height="5" viewBox="0 0 10 10"><circle cx="5" cy="5" r="5" fill="#fff"/><path d="M4 2.5 6.5 5 4 7.5" fill="none" stroke="#b5651d" stroke-width="1.6"/></svg></span>
        </article>
        <div class="offer-visual" role="img" aria-label="Line drawing of a hand holding a pen"></div>
        <article class="offer-card">
          <h3 class="offer-card__title">Book Development</h3>
          <p class="offer-card__text">At vero eos et accusamus et iusto odio dignissiducimumos ducimus qui blanditiis pducimuducimuraesentiu</p>
          <span class="btn btn--small">Read more <svg width="5" height="5" viewBox="0 0 10 10"><circle cx="5" cy="5" r="5" fill="#fff"/><path d="M4 2.5 6.5 5 4 7.5" fill="none" stroke="#b5651d" stroke-width="1.6"/></svg></span>
        </article>
      </div>
    </section>

    <section class="about">
      <h2 class="section-title">ABOUT US</h2>
      <p class="about__text">Lorem ipsum dolor sit amet, consectetur adipiscing elit, sed do eiusmod tempor incididunt ut labore et dolore magna aliqua. Quis ipsum suspendisse ultrices gravida. Risus commodo viverra maecenas accumsan lacus vel facilisisLorem ipsum dolor sit amet, consectetur adipiscing elit, sed do eiusmod tempor incididunt ut labore et dolore magna aliqua. Quis ipsum suspendisse ultrices gravida. Risus commodo viverra maecenas accumsan lacus vel facilisis. Lorem ipsum dolor sit amet, consectetur adipiscing elit, sed do eiusmod tempor incididunt ut labore et dolore magna aliqua.is ipsum suspendisse ultrices gravida</p>
      <span class="btn btn--large">Read more <svg width="6" height="6" viewBox="0 0 10 10"><circle cx="5" cy="5" r="5" fill="#fff"/><path d="M4 2.5 6.5 5 4 7.5" fill="none" stroke="#b5651d" stroke-width="1.6"/></svg></span>
    </section>

    <section class="contact">
      <div class="contact__scene" role="img" aria-label="Misty lavender lake at dawn with a person stretching on the shore"></div>
      <h2 class="section-title">CONTACT FORM</h2>
      <form class="contact-form">
        <div class="field field--first">First Name</div>
        <div class="field field--last">Last Name</div>
        <div class="field field--email">Email address</div>
        <div class="field field--phone">Phone Number</div>
        <div class="field field--message">Message</div>
      </form>
      <span class="btn btn--large">Submit <svg width="6" height="6" viewBox="0 0 10 10"><circle cx="5" cy="5" r="5" fill="#fff"/><path d="M4 2.5 6.5 5 4 7.5" fill="none" stroke="#b5651d" stroke-width="1.6"/></svg></span>
    </section>

    <footer class="site-footer">
      <div class="brand"><span class="brand__dot"></span><span class="brand__name">DWB Productions</span></div>
      <div class="footer-contacts">
        <div class="footer-contacts__item"><span class="footer-contacts__icon"><svg width="6" height="7" viewBox="0 0 12 14"><path d="M6 13S1 7.5 1 5a5 5 0 0 1 10 0c0 2.5-5 8-5 8z" fill="#fff"/><circle cx="6" cy="5" r="1.8" fill="#2d2d2d"/></svg></span><span>314,At vero eos et accu<br>samus et iusto odio dimos ducimu</span></div>
        <div class="footer-contacts__item"><span class="footer-contacts__icon"><svg width="6" height="6" viewBox="0 0 12 12"><path d="M2.5 1 4.5 3.5 3.3 5a7 7 0 0 0 3.7 3.7L8.5 7.5 11 9.5 10 11C5 11 1 7 1 2z" fill="#fff"/></svg></span><span>1 888 888 8888</span></div>
        <div class="footer-contacts__item"><span class="footer-contacts__icon"><svg width="7" height="5" viewBox="0 0 14 10"><rect width="14" height="10" rx="1" fill="#fff"/><path d="M1 1.5 7 6 13 1.5" fill="none" stroke="#2d2d2d" stroke-width="1.2"/></svg></span><span>info@dorawhitbyproductions.com</span></div>
      </div>
      <nav class="footer-nav"><span>Home</span> / <span>About</span> / <span>Services</span> / <span>News</span> / <span>Contact</span></nav>
      <p class="copyright">© 2021 DWB Productions. All rights reserved.Privacy Terms of Use</p>
    </footer>
  </section>

</main>
</body>
</html>
```